Local Roofing/Construction company business needs new biz card design

We need a new business card design, current cards are from the start of this operation and generic at best. We are a local Construction Company (General Contractor) with a majority of our work originating from insurance claims-exterior finish work is the main focus (Roofs-Siding-Gutters etc). Heavily involved with homeowners and the low ball offers they receive from insurance company's after a insurable event takes place. I have attached some of our original logo file(s) below.

```html
<!DOCTYPE html>
<html lang="en">
<head>
<meta charset="utf-8">
<title>Stonebay Construction – Business Card</title>
<link href="https://fonts.googleapis.com/css2?family=Montserrat:wght@400;500;700;800&display=swap" rel="stylesheet">
<style>
  :root {
    --backdrop: #d3d6d6;
    --paper: #fbfbfa;
    --brand-green: #1f9a3c;
    --ink: #2b2b2b;
    --muted: #555;
  }
  * { box-sizing: border-box; margin: 0; padding: 0; }
  html, body { width: 1200px; height: 829px; overflow: hidden; }
  body {
    background: var(--backdrop);
    font-family: "Montserrat", sans-serif;
    position: relative;
  }
  .card {
    position: absolute;
    top: 266px;
    width: 520px;
    height: 297px;
    background: var(--paper);
    border-bottom: 4px solid var(--brand-green);
    box-shadow: 0 10px 24px rgba(0,0,0,0.18);
  }
  .card-front { left: 50px; }
  .card-back  { left: 630px; }

  /* Front */
  .brand-line {
    position: absolute;
    top: 40px;
    left: 150px;
    display: flex;
    align-items: center;
    gap: 10px;
    color: var(--brand-green);
    font-weight: 800;
    font-size: 22px;
    letter-spacing: 0.5px;
    text-transform: uppercase;
  }
  .brand-mark {
    width: 18px; height: 18px;
    background: var(--brand-green);
  }
  .person {
    position: absolute;
    top: 128px;
    right: 280px;
    text-align: right;
  }
  .person-name {
    color: var(--brand-green);
    font-weight: 700;
    font-size: 17px;
    letter-spacing: 0.6px;
    text-transform: uppercase;
  }
  .person-role {
    color: var(--muted);
    font-size: 11px;
    margin-top: 3px;
  }
  .divider {
    position: absolute;
    top: 124px;
    left: 254px;
    width: 1px;
    height: 64px;
    background: var(--brand-green);
  }
  .contact-list {
    position: absolute;
    top: 124px;
    left: 270px;
    list-style: none;
  }
  .contact-list li {
    display: flex;
    align-items: center;
    gap: 8px;
    font-size: 12.5px;
    color: var(--ink);
    line-height: 22px;
  }
  .contact-icon { width: 12px; height: 12px; flex: none; }
  .address {
    position: absolute;
    left: 0; right: 0;
    bottom: 48px;
    text-align: center;
    font-size: 12.5px;
    color: var(--ink);
  }

  /* Back */
  .back-brand {
    position: absolute;
    inset: 0;
    display: flex;
    flex-direction: column;
    align-items: center;
    justify-content: center;
    gap: 14px;
    color: var(--brand-green);
    font-weight: 800;
    font-size: 24px;
    text-transform: uppercase;
    letter-spacing: 0.6px;
  }
  .back-mark {
    width: 34px; height: 34px;
    background: var(--brand-green);
  }
</style>
</head>
<body>

<section class="card card-front" aria-label="Card front">
  <div class="brand-line">
    <span class="brand-mark"></span>
    <span>Stonebay Construction</span>
  </div>

  <div class="person">
    <p class="person-name">Dale Harmon</p>
    <p class="person-role">Managing Director</p>
  </div>

  <div class="divider"></div>

  <ul class="contact-list">
    <li>
      <svg class="contact-icon" viewBox="0 0 12 12" aria-hidden="true">
        <circle cx="6" cy="6" r="6" fill="var(--brand-green)"/>
        <path d="M4 3.2 5 4.4 4.5 5.2Q5.3 6.8 6.8 7.5L7.6 7 8.8 8 8.2 8.9Q5.6 8.6 3.2 5 3 3.8 4 3.2Z" fill="#fff"/>
      </svg>
      0400 555 019
    </li>
    <li>
      <svg class="contact-icon" viewBox="0 0 12 12" aria-hidden="true">
        <circle cx="6" cy="6" r="6" fill="var(--brand-green)"/>
        <rect x="3" y="4" width="6" height="4.2" fill="#fff"/>
        <path d="M3 4 6 6.3 9 4" fill="none" stroke="var(--brand-green)" stroke-width="0.7"/>
      </svg>
      info@stonebaybuild.com
    </li>
    <li>
      <svg class="contact-icon" viewBox="0 0 12 12" aria-hidden="true">
        <circle cx="6" cy="6" r="6" fill="var(--brand-green)"/>
        <circle cx="6" cy="6" r="3" fill="none" stroke="#fff" stroke-width="0.8"/>
        <path d="M3 6H9M6 3Q4.5 6 6 9Q7.5 6 6 3" fill="none" stroke="#fff" stroke-width="0.7"/>
      </svg>
      www.stonebaybuild.com
    </li>
  </ul>

  <p class="address">1450 W Harbor Road Millbrook County Name 4120</p>
</section>

<section class="card card-back" aria-label="Card back">
  <div class="back-brand">
    <span class="back-mark"></span>
    <span>Stonebay Construction</span>
  </div>
</section>

</body>
</html>
```